Quick Straightforward Billboard Redesign

- Design billboard sized for 10 foot' x 36' foot width live area size and please include bleeds 6" around all sides
- Exact blue color match is imperative in headline, logo, phone number bubble or wherever used. C-83 / M-45 / Y-1 / K-0-
- What I hope to illustrate is that our company offers the best porch screening in the area area, in regards to quality, expertise, durability, storms proof, but we do not build screen porches.
- Current board is attached below from previous designer, and as you can see sizing was off, white space on edges make it appear to be sized incorrectly.
- I also attached my own little mock up idea well well if it helps, favorite image, logo, headline, etc and ideas perhaps on expanding or making this better?

Thanks so much!

Target Market(s)

Drivers and passengers, Southeastern NC, are of immense new construction and high end homes.

Industry/Entity Type

Construction

Colors
0054AA
0677BA
7BADD7
CADEEF
E8F1F8

Requirements
Must have
• Blue color matching
Nice to have
• Design spins or other thoughts on my little mock up

```html
<!DOCTYPE html>
<html lang="en">
<head>
<meta charset="utf-8">
<title>Harborline Screens – Billboard</title>
<link rel="stylesheet" href="https://fonts.googleapis.com/css2?family=Jost:wght@700&family=Roboto+Condensed:wght@500;800&display=swap">
<style>
  :root {
    --brand-blue: #0054aa;
    --blue-mid: #0a62b8;
    --blue-deep: #0a4f9a;
    --coast-green: #00b960;
    --white: #ffffff;
    --cream: #f3eee2;
    --stage: #dedede;
  }
  html, body {
    margin: 0;
    padding: 0;
    width: 1145px;
    height: 1200px;
    overflow: hidden;
    background: var(--stage);
  }
  .canvas {
    position: relative;
    width: 1145px;
    height: 1200px;
  }
  .billboard {
    position: absolute;
    left: 50px;
    top: 442px;
    width: 1045px;
    height: 315px;
    box-shadow: 0 6px 14px rgba(0,0,0,0.35);
  }
  .headline {
    font-family: "Jost", "Futura", sans-serif;
    font-weight: 700;
    fill: var(--white);
  }
  .brand-name {
    font-family: "Roboto Condensed", "Arial Narrow", sans-serif;
    font-weight: 500;
    fill: var(--cream);
  }
  .phone-number {
    font-family: "Roboto Condensed", "Arial Narrow", sans-serif;
    font-weight: 800;
    fill: var(--brand-blue);
  }
</style>
</head>
<body>
<div class="canvas">
  <svg class="billboard" viewBox="0 0 1588 478" xmlns="http://www.w3.org/2000/svg">
    <defs>
      <linearGradient id="porch-tint" x1="0" y1="0" x2="1" y2="1">
        <stop offset="0" stop-color="#1464b4"/>
        <stop offset="0.5" stop-color="#0f5cab"/>
        <stop offset="1" stop-color="#0b4f9c"/>
      </linearGradient>
    </defs>

    <rect class="porch-photo" x="0" y="0" width="1588" height="478" fill="url(#porch-tint)" role="img" aria-label="Blue-tinted photo of a screened porch with wicker seating and palm fronds"/>

    <text class="headline" x="66" y="141" font-size="140" textLength="1460" lengthAdjust="spacingAndGlyphs">SCREEN YOUR PORCH.</text>

    <rect class="green-band" x="0" y="176" width="1588" height="120" fill="var(--coast-green)"/>
    <text class="headline" x="72" y="281" font-size="140" textLength="1454" lengthAdjust="spacingAndGlyphs">BUILT FOR THE COAST.</text>

    <g class="brand">
      <rect class="brand-square" x="74" y="368" width="62" height="62" fill="var(--cream)"/>
      <text class="brand-name" x="160" y="432" font-size="82" textLength="642" lengthAdjust="spacingAndGlyphs">HARBORLINE SCREENS</text>
    </g>

    <g class="phone-bubble">
      <path d="M859 316 H1588 V436 H859 Q839 436 839 416 V336 Q839 316 859 316 Z" fill="var(--white)"/>
      <circle cx="894" cy="376" r="37" fill="var(--coast-green)" stroke="#e6efe9" stroke-width="4"/>
      <path class="phone-icon" d="M880 356 q-6 4 -4 12 q6 20 24 30 q8 4 12 -2 l3 -5 q1 -3 -2 -5 l-8 -5 q-3 -2 -5 1 l-3 3 q-9 -5 -13 -13 l3 -3 q3 -2 1 -5 l-5 -8 q-2 -3 -5 -2 z" fill="var(--white)"/>
      <path d="M899 360 a10 10 0 0 1 9 9 M899 352 a18 18 0 0 1 17 17" fill="none" stroke="var(--white)" stroke-width="3.5" stroke-linecap="round"/>
      <text class="phone-number" x="955" y="420" font-size="118" textLength="570" lengthAdjust="spacingAndGlyphs">555.014.2288</text>
    </g>
  </svg>
</div>
</body>
</html>
```